NZ First of it's kind solutions directory and marketplace for busy Mums needs a business card design

We need a business card design for our new nationwide business in NZ (long term plans to go global). We provide solutions to the everyday challenges that busy Mums face by connecting them with quality communities and suppliers of carefully selected, relevant products and services. We sell direct via our online marketplace. The final design should communicate our values of inclusivity, quality and smart solutions. Colours should incorporate our logo colour palette of #477077 and #6ba8b2. Our website is at https://www.brightnestmums.example

Target Market(s)

busy Mums, Age 28 – 50, female, income over $100K, location main centres NZ primarily but NZ wide. Is likely juggling work or career with a young family. Probably had hobbies which have fallen by the wayside.
-Wants to succeed in her chosen career without compromising on family life
-to successfully juggle her career without feeling like she is compromising her children
- Is time poor, something always has to give and it’s generally her health (she’ll stay up late, get stressed)
- probably ex corporate or professional career. Has discretional income

Industry/Entity Type

Business

Contact Information for Business Card

Lena Forbisher, Founder, BrightNestMums.example (Strapline Tap; Gather; Sorted), 47 Kowhai Terrace, Ellerslie, Auckland 1051, New Zealand. Mob: 021 483 517 Ph: +64 (0)9 571 4860

Font styles to use
Other font styles liked:
• Raleway, and/or Architects Daughter

Colors
00a990
33b8a4
86cfc6
cfeae6

Requirements
Must have
• the above details, streamline. the logo and colours associated with those logos
Should not have
• foil or metallic colours

```html
<!DOCTYPE html>
<html lang="en">
<head>
<meta charset="utf-8">
<title>BrightNestMums business card</title>
<link rel="stylesheet" href="https://fonts.googleapis.com/css2?family=Nunito:ital,wght@0,800;1,400&family=Roboto:ital,wght@0,400;1,400&display=swap">
<style>
  :root {
    --brand-dark: #477077;
    --brand-light: #6ba8b2;
    --ink: #3b4447;
    --card: #ffffff;
    --card-shade: #f0f1f1;
    --backdrop: #e4e5e5;
  }
  * { box-sizing: border-box; margin: 0; padding: 0; }
  html, body { width: 1200px; height: 576px; overflow: hidden; }
  body {
    background: var(--backdrop);
    position: relative;
    font-family: "Roboto", Arial, sans-serif;
    color: var(--ink);
  }
  .card {
    position: absolute;
    top: 138px;
    width: 484px;
    height: 294px;
    border-radius: 11px;
    overflow: hidden;
    background: linear-gradient(160deg, var(--card) 0%, var(--card-shade) 100%);
    box-shadow: 0 2px 6px rgba(0,0,0,0.18);
  }
  .card--front { left: 82px; }
  .card--back { left: 602px; width: 481px; }

  /* Front */
  .front-mark {
    position: absolute;
    left: 14px;
    top: 66px;
    width: 180px;
    height: 180px;
    border-radius: 50%;
    background: var(--brand-dark);
  }
  .wordmark {
    font-family: "Nunito", Arial, sans-serif;
    font-weight: 800;
    color: var(--brand-dark);
    letter-spacing: -0.5px;
    white-space: nowrap;
  }
  .front-wordmark {
    position: absolute;
    right: 28px;
    top: 196px;
    font-size: 31px;
  }
  .strapline {
    position: absolute;
    right: 30px;
    top: 240px;
    font-size: 11px;
    letter-spacing: 3.4px;
    color: var(--ink);
    white-space: nowrap;
  }
  .strapline .divider { color: var(--brand-light); padding: 0 4px; }

  /* Back */
  .back-brand {
    position: absolute;
    left: 30px;
    top: 58px;
    display: flex;
    align-items: center;
    gap: 12px;
  }
  .back-brand .dot {
    width: 34px;
    height: 34px;
    border-radius: 50%;
    background: var(--brand-dark);
  }
  .back-brand .wordmark { font-size: 32px; }

  .person { position: absolute; left: 36px; top: 212px; }
  .person-name {
    font-family: "Nunito", Arial, sans-serif;
    font-weight: 800;
    font-size: 20px;
    color: var(--brand-dark);
  }
  .person-role { font-style: italic; font-size: 12px; margin-top: 2px; }

  .contact { position: absolute; left: 269px; top: 136px; font-size: 12.3px; line-height: 18px; }
  .contact-address { margin-bottom: 8px; }
  .contact-list { list-style: none; }
  .contact-list li { display: flex; align-items: center; gap: 8px; }
  .contact-list svg { width: 11px; height: 11px; fill: var(--brand-dark); flex: none; }

  .band-stripe {
    position: absolute;
    left: 0; bottom: 7px;
    width: 240px; height: 8px;
    background: var(--brand-light);
  }
  .band-tab {
    position: absolute;
    left: 220px; bottom: 0;
    width: 261px; height: 39px;
    background: var(--brand-dark);
    clip-path: polygon(18px 0, 100% 0, 100% 100%, 0 100%);
  }
  .website {
    position: absolute;
    left: 269px; bottom: 12px;
    font-size: 12.3px;
    color: #ffffff;
  }
</style>
</head>
<body>

<section class="card card--front" aria-label="Card front">
  <div class="front-mark"></div>
  <div class="wordmark front-wordmark">BrightNestMums</div>
  <div class="strapline">TAP<span class="divider">|</span>GATHER<span class="divider">|</span>SORTED</div>
</section>

<section class="card card--back" aria-label="Card back">
  <div class="back-brand">
    <span class="dot"></span>
    <span class="wordmark">BrightNestMums</span>
  </div>

  <div class="person">
    <div class="person-name">Lena Forbisher</div>
    <div class="person-role">Founder</div>
  </div>

  <div class="contact">
    <p class="contact-address">47 Kowhai Terrace, Ellerslie,<br>Auckland 1051, New Zealand</p>
    <ul class="contact-list">
      <li>
        <svg viewBox="0 0 12 12" aria-hidden="true"><path d="M3 0h6a1 1 0 0 1 1 1v10a1 1 0 0 1-1 1H3a1 1 0 0 1-1-1V1a1 1 0 0 1 1-1zm0 1.5v7.5h6V1.5zm3 8.3a.7.7 0 1 0 0 1.4.7.7 0 0 0 0-1.4z"/></svg>
        021 483 517
      </li>
      <li>
        <svg viewBox="0 0 12 12" aria-hidden="true"><path d="M1 3.5C1 2 3 1.5 6 1.5S11 2 11 3.5V5H8.5V4h-5v1H1zM3 6h6l1.5 5h-9z"/></svg>
        +64 (0)9 571 4860
      </li>
      <li>
        <svg viewBox="0 0 12 12" aria-hidden="true"><path d="M0 2.5h12v7H0zm1 1v.3l5 3.2 5-3.2v-.3zm0 1.5v3.5h10V5L6 8.2z"/></svg>
        lena@brightnestmums.example
      </li>
    </ul>
  </div>

  <div class="band-stripe"></div>
  <div class="band-tab"></div>
  <div class="website">www.BrightNestMums.example</div>
</section>

</body>
</html>
```